To design a brand identity that is simple and creative with 'Corvane' as the brand name, I like modern simple fonts like helvetica neue, I want to print both sides of the card, I am open to dark front and white back, but the design needs to transfer well to letter heads and email signatures, I am looking for sophisticated and elegant, but open minded about clever and off the wall, I do not do 'boring' Corvane Ventures is the mother company for a small group, specialising in Management & consulting, Software development and construction, we have a high level of integrity, we are transparent and accountable for what we do. my images are provided as a guide only, Im not expecting them to be just copied, Im looking for a creator and passionate thinker, who will put life into their work.

Target Market(s)

usually business minded people who are looking for something different in me, such as leadership, confidence and focus with thinking that is per haps a little outside the box..

Industry/Entity Type

Construction

Requirements
Must have
• clean, minmalistic
Nice to have
• custom logo
Should not have
• boring, traditional

```html
<!DOCTYPE html>
<html lang="en">
<head>
<meta charset="utf-8">
<title>Corvane Ventures — Business Card</title>
<link rel="stylesheet" href="https://fonts.googleapis.com/css2?family=Inter:wght@300;400&display=swap">
<style>
  :root {
    --stage: #2f2b29;
    --card: #ffffff;
    --brand-orange: #e8664a;
    --ink: #1c1c1c;
    --muted: #c9c9c9;
    --tagline: #6a6a6a;
    --label: #e6e6e6;
    --on-gradient: #ffffff;
  }
  * { box-sizing: border-box; margin: 0; padding: 0; }
  html, body {
    width: 1000px; height: 1200px; overflow: hidden;
    background: var(--stage);
    font-family: "Inter", "Helvetica Neue", Arial, sans-serif;
  }
  .canvas { position: relative; width: 1000px; height: 1200px; }

  .card {
    position: absolute;
    width: 722px; height: 423px;
    background: var(--card);
    overflow: hidden;
  }
  .card--front { left: 145px; top: 95px; }
  .card--back { left: 125px; top: 652px; }

  .card__band { position: absolute; inset: 0; width: 722px; height: 423px; }

  .brand { position: absolute; display: flex; flex-direction: column; align-items: flex-start; }
  .brand__row { display: flex; align-items: center; gap: 14px; }
  .brand__mark { width: 36px; height: 36px; border-radius: 50%; background: var(--brand-orange); }
  .brand__name {
    font-weight: 400; font-size: 40px; line-height: 1;
    color: var(--brand-orange); letter-spacing: 1px;
  }
  .brand__tagline {
    margin-top: 12px; margin-left: 52px;
    font-weight: 300; font-size: 12px; letter-spacing: 0.3px; color: var(--tagline);
  }
  .card--front .brand { left: 62px; top: 175px; }
  .card--back .brand { left: 246px; top: 175px; }

  .contact {
    position: absolute; right: 35px; top: 54px;
    text-align: right; color: var(--on-gradient); font-weight: 300;
  }
  .contact__name { font-size: 31px; line-height: 1.1; }
  .contact__role { font-size: 17px; margin-top: 6px; }
  .contact__details { margin-top: 76px; font-size: 19px; line-height: 30px; }
  .contact__details .small { font-size: 18px; }

  .services {
    position: absolute; display: flex; align-items: center;
    font-size: 21px; letter-spacing: 2px; font-weight: 300;
  }
  .services__dot { width: 5px; height: 5px; border-radius: 50%; }
  .card--front .services { left: 72px; top: 358px; }
  .card--front .services__item--lead { color: var(--ink); font-weight: 400; }
  .card--front .services__item--alt { color: var(--on-gradient); }
  .card--front .services__dot { background: var(--on-gradient); }
  .card--back .services { left: 107px; top: 254px; color: var(--muted); letter-spacing: 2.2px; }
  .card--back .services__dot { background: var(--muted); }

  .side-label {
    position: absolute; font-size: 20px; font-weight: 300; color: var(--label);
  }
  .side-label--front { left: 811px; top: 569px; }
  .side-label--back { left: 117px; top: 1143px; color: #bdbdbd; }
</style>
</head>
<body>
<main class="canvas">

  <section class="card card--front" aria-label="Card front">
    <svg class="card__band" viewBox="0 0 722 423" aria-hidden="true">
      <defs>
        <linearGradient id="bandBase" gradientUnits="userSpaceOnUse" x1="400" y1="0" x2="722" y2="0">
          <stop offset="0" stop-color="#f2a459"/>
          <stop offset="0.35" stop-color="#efb062"/>
          <stop offset="0.7" stop-color="#908070"/>
          <stop offset="1" stop-color="#3c7873"/>
        </linearGradient>
        <linearGradient id="bandWarm" gradientUnits="userSpaceOnUse" x1="230" y1="423" x2="520" y2="150">
          <stop offset="0" stop-color="#e0363f" stop-opacity="1"/>
          <stop offset="0.4" stop-color="#ec6d48" stop-opacity="0.85"/>
          <stop offset="1" stop-color="#f2a459" stop-opacity="0"/>
        </linearGradient>
      </defs>
      <polygon points="505,0 722,0 722,423 215,423" fill="url(#bandBase)"/>
      <polygon points="505,0 722,0 722,423 215,423" fill="url(#bandWarm)"/>
    </svg>

    <div class="brand">
      <div class="brand__row">
        <span class="brand__mark"></span>
        <span class="brand__name">Corvane</span>
      </div>
      <span class="brand__tagline">built with integrity, made to last</span>
    </div>

    <div class="contact">
      <p class="contact__name">mara lindqvist</p>
      <p class="contact__role">client ambassador</p>
      <div class="contact__details">
        <p>m. +61 0400 512 907</p>
        <p class="small">po box 418 perth 6150</p>
        <p>w. www.corvane.com.au</p>
      </div>
    </div>

    <div class="services">
      <span class="services__item services__item--lead">management</span>
      <span class="services__dot" style="margin:0 44px 0 45px"></span>
      <span class="services__item services__item--alt">software</span>
      <span class="services__dot" style="margin:0 45px 0 44px"></span>
      <span class="services__item services__item--alt">construction</span>
    </div>
  </section>
  <p class="side-label side-label--front">Front</p>

  <section class="card card--back" aria-label="Card back">
    <div class="brand">
      <div class="brand__row">
        <span class="brand__mark"></span>
        <span class="brand__name">Corvane</span>
      </div>
      <span class="brand__tagline">built with integrity, made to last</span>
    </div>

    <div class="services">
      <span class="services__item">management</span>
      <span class="services__dot" style="margin:0 27px"></span>
      <span class="services__item">software</span>
      <span class="services__dot" style="margin:0 27px"></span>
      <span class="services__item">construction</span>
    </div>
  </section>
  <p class="side-label side-label--back">Back</p>

</main>
</body>
</html>
```